Business Card Design

New business card design

Target Market(s)

Residential & Commercial Property Managers

Industry/Entity Type

Plumbing Services

Contact Information for Business Card

Name - Rowan Keddle, title - Director, Phone Number - 0431 286 517, email - rowan@tbk-plumbing.com.au, Company ABN - 73 215 904 386,

Font styles to use
Sans Serif

Colors
0054AA
0677BA
7BADD7
CADEEF
E8F1F8

```html
<!DOCTYPE html>
<html lang="en">
<head>
<meta charset="UTF-8">
<title>TBK Plumbing Services – Business Card</title>
<link rel="stylesheet" href="https://fonts.googleapis.com/css2?family=Montserrat:wght@400;500;700&display=swap">
<style>
  :root {
    --backdrop: #e7e6e7;
    --card-white: #ffffff;
    --ink: #1e232c;
    --navy: #1e232c;
    --sky: #2ba7e0;
    --brand-blue: #3d6fb8;
  }
  * { box-sizing: border-box; margin: 0; padding: 0; }
  html, body {
    width: 1200px; height: 1108px; overflow: hidden;
    background: var(--backdrop);
    font-family: "Montserrat", sans-serif;
    color: var(--ink);
  }
  .canvas { position: relative; width: 1200px; height: 1108px; }

  .card { position: absolute; left: 236px; width: 740px; height: 446px; overflow: hidden; }
  .card--front { top: 61px; background: var(--card-white); }
  .card--back { top: 580px; background: var(--navy); }

  .brand {
    position: absolute; display: flex; align-items: center; gap: 8px;
    font-weight: 500; white-space: nowrap; transform: translateX(-50%);
  }
  .brand__dot { border-radius: 50%; background: var(--sky); flex: none; }
  .card--front .brand { left: 200px; top: 238px; font-size: 20px; line-height: 24px; color: var(--ink); }
  .card--front .brand__dot { width: 12px; height: 12px; }

  .divider {
    position: absolute; left: 368px; top: 148px; width: 2px; height: 186px;
    background: var(--ink);
  }
  .contact { position: absolute; left: 387px; top: 146px; }
  .contact__name { font-size: 26px; font-weight: 700; line-height: 1.2; }
  .contact__title { font-size: 16px; font-weight: 500; margin-top: 1px; }
  .contact__list { list-style: none; margin-top: 18px; }
  .contact__item {
    display: flex; align-items: center; gap: 10px;
    font-size: 16px; height: 31px;
  }
  .contact__item svg { width: 17px; height: 17px; fill: var(--ink); flex: none; }
  .contact__abn { font-size: 16px; margin-top: 1px; }
  .contact__abn strong { font-weight: 700; }

  .band { position: absolute; left: 0; bottom: 0; width: 740px; height: 26px; }

  .card--back .brand {
    left: 50%; top: 200px;
    font-size: 44px; color: var(--brand-blue);
  }
  .card--back .brand__dot { width: 26px; height: 26px; }
  .back-rule {
    position: absolute; right: 0; bottom: 0; width: 386px; height: 2px;
    background: var(--sky);
  }
</style>
</head>
<body>
<main class="canvas">
  <section class="card card--front" aria-label="Business card front">
    <div class="brand">
      <span class="brand__dot"></span>
      <span class="brand__name">TBK Plumbing Services</span>
    </div>
    <div class="divider"></div>
    <div class="contact">
      <h1 class="contact__name">Rowan Keddle</h1>
      <p class="contact__title">Director</p>
      <ul class="contact__list">
        <li class="contact__item">
          <svg viewBox="0 0 24 24" aria-hidden="true"><path d="M6.6 10.8a15.1 15.1 0 0 0 6.6 6.6l2.2-2.2a1 1 0 0 1 1-.25 11.4 11.4 0 0 0 3.6.57 1 1 0 0 1 1 1V20a1 1 0 0 1-1 1A17 17 0 0 1 3 4a1 1 0 0 1 1-1h3.5a1 1 0 0 1 1 1c0 1.250.2 2.450.57 3.6a1 1 0 0 1-.25 1z"/></svg>
          <span>0431 286 517</span>
        </li>
        <li class="contact__item">
          <svg viewBox="0 0 24 24" aria-hidden="true"><path d="M3 6h18v1.2l-9 5.6-9-5.6zM3 9.5l9 5.6 9-5.6V18H3z"/></svg>
          <span>rowan@tbk-plumbing.com.au</span>
        </li>
        <li class="contact__item">
          <svg viewBox="0 0 24 24" aria-hidden="true"><path d="M12 2a10 10 0 1 0 0 20 10 10 0 0 0 0-20zm-1 17.9A8 8 0 0 1 4.2 10L9 14.8v1a2 2 0 0 0 2 2zm6.9-2.5A2 2 0 0 0 16 16h-1v-3a1 1 0 0 0-1-1H8v-2h2a1 1 0 0 0 1-1V7h2a2 2 0 0 0 2-2v-.4a8 8 0 0 1 2.9 12.8z"/></svg>
          <span>www.tbk-plumbing.com.au</span>
        </li>
      </ul>
      <p class="contact__abn"><strong>ABN</strong> - 73 215 904 386,</p>
    </div>
    <svg class="band" viewBox="0 0 740 26" preserveAspectRatio="none" aria-hidden="true">
      <polygon points="0,0 370,0 350,26 0,26" fill="var(--navy)"/>
      <polygon points="380,0 740,0 740,26 360,26" fill="var(--sky)"/>
    </svg>
  </section>

  <section class="card card--back" aria-label="Business card back">
    <div class="brand">
      <span class="brand__dot"></span>
      <span class="brand__name">TBK Plumbing Services</span>
    </div>
    <div class="back-rule"></div>
  </section>
</main>
</body>
</html>
```